Small Business Broker Business Card Design

A business card design for a small business brokerage, which is a financial service, not unlike real estate brokerage, but for small businesses such as laundromats, pizza shops, restaurants, cleaners etc. The designs should all be simple, more conservative in nature, using the colors and font of the logo. Again, think real estate Brokerage as a business context
Contact Information for Business Card
Name: Glen R. Harlow. Title: Small Business Advisor. Email: g.harlow@bayfieldcapitalworks.example. Mobile: (555) 274-3918. Office: (555) 806-2147. www.bayfieldcapitalworks.example

```html
<!DOCTYPE html>
<html lang="en">
<head>
<meta charset="utf-8">
<title>Bayfield Capital Works – Business Card</title>
<link rel="stylesheet" href="https://fonts.googleapis.com/css2?family=Josefin+Sans:wght@700&family=Montserrat:wght@400;500;600&display=swap">
<style>
  :root {
    --navy: #1c3769;
    --green: #8cc63f;
    --ink: #1e1e1e;
    --paper: #ffffff;
    --backdrop: #d3d3d3;
  }
  * { margin: 0; padding: 0; box-sizing: border-box; }
  html, body { width: 1093px; height: 1200px; overflow: hidden; }
  body {
    position: relative;
    background: var(--backdrop);
    font-family: "Montserrat", Arial, sans-serif;
    color: var(--ink);
  }
  .card {
    position: absolute;
    left: 265px;
    width: 580px;
    height: 364px;
    background: var(--paper);
  }
  .card--front { top: 225px; }
  .card--back  { top: 615px; }

  .brand-square {
    position: absolute;
    background: var(--navy);
  }
  .card--front .brand-square { left: 110px; top: 108px; width: 96px; height: 96px; }
  .card--back  .brand-square { left: 243px; top: 112px; width: 94px; height: 94px; }

  .divider {
    position: absolute;
    left: 246px; top: 80px;
    width: 1.5px; height: 157px;
    background: var(--navy);
  }
  .person {
    position: absolute;
    left: 258px; top: 76px;
  }
  .person__name {
    font-family: "Josefin Sans", Arial, sans-serif;
    font-weight: 700;
    font-size: 25px;
    line-height: 1;
    color: var(--navy);
    letter-spacing: 0.2px;
  }
  .person__title {
    margin-top: 3px;
    font-size: 13px;
    font-weight: 400;
  }
  .contacts {
    position: absolute;
    left: 258px; top: 142px;
    list-style: none;
    font-size: 12.6px;
  }
  .contacts li {
    height: 26.5px;
    display: flex;
    align-items: center;
    white-space: nowrap;
  }
  .contacts .label {
    flex: 0 0 20px;
    font-weight: 600;
    color: var(--navy);
  }

  .company {
    position: absolute;
    left: 0; right: 0;
    text-align: center;
  }
  .company__name {
    font-family: "Josefin Sans", Arial, sans-serif;
    font-weight: 700;
    color: var(--navy);
    line-height: 1;
    white-space: nowrap;
  }
  .company__tagline {
    font-weight: 600;
    color: var(--green);
    text-transform: uppercase;
    white-space: nowrap;
    line-height: 1;
  }
  .card--front .company { top: 290px; }
  .card--front .company__name { font-size: 26px; letter-spacing: 0.4px; }
  .card--front .company__tagline { font-size: 11.6px; letter-spacing: 2.2px; margin-top: 3px; }
  .card--back .company { top: 230px; }
  .card--back .company__name { font-size: 24px; letter-spacing: 0.2px; }
  .card--back .company__tagline { font-size: 10.8px; letter-spacing: 2px; margin-top: 2px; }
</style>
</head>
<body>
  <section class="card card--front">
    <div class="brand-square"></div>
    <div class="divider"></div>
    <div class="person">
      <h1 class="person__name">GLEN R. HARLOW</h1>
      <p class="person__title">Small Business Advisor</p>
    </div>
    <ul class="contacts">
      <li><span class="label">M:</span>(555) 274-3918</li>
      <li><span class="label">O:</span>(555) 806-2147</li>
      <li><span class="label">E:</span>g.harlow@bayfieldcapitalworks.example</li>
      <li><span class="label">W:</span>www.bayfieldcapitalworks.example</li>
    </ul>
    <div class="company">
      <p class="company__name">BAYFIELD CAPITAL WORKS, INC</p>
      <p class="company__tagline">Securely buy or sell a main street business now</p>
    </div>
  </section>

  <section class="card card--back">
    <div class="brand-square"></div>
    <div class="company">
      <p class="company__name">BAYFIELD CAPITAL WORKS, INC</p>
      <p class="company__tagline">Securely buy or sell a main street business now</p>
    </div>
  </section>
</body>
</html>
```